Cleaning service website design

We need a new nice web design(logo will be the same) for a new cleaning service Company:

Informations about Company and logo you can take from flyers in attachments.

This is a cleaning service Company which have simple rules and we would like to show that(in checklist form) on website:

- What we do and that we're Cleaning Green

- Why us?

- How much(our pricing is simple)

Also we would like to communicate with clients by some nice/big pictures on website and the most important thing is our phone number and short/fast Brimtallow.

Also there should be some space for description about our Company.

Generally all information on main page can be short: about us, about service(what we do), last reviews, tips (for example: Tip of the week) and other can be some introduction to subpage where will be more information.

There will be few subpages like: About us, About our service, Photos(Before and after), Reviews , Tips, FAQ, Contact, Looking for a Job? - most of them will be just text so you can project just one example.

```html
<!DOCTYPE html>
<html lang="en">
<head>
<meta charset="utf-8">
<title>Tidy Nest House Cleaning</title>
<link rel="stylesheet" href="https://fonts.googleapis.com/css2?family=Montserrat:wght@400;500;600;700&family=Open+Sans:wght@400;600&family=Playfair+Display:ital@1&family=Kaushan+Script&family=Oswald:wght@500&display=swap">
<style>
:root{
  --blue:#0a56a9;
  --blue-dark:#074a94;
  --blue-line:#2f7ccc;
  --green:#6cbf5a;
  --green-dark:#4aa63c;
  --script-green:#2a9a2a;
  --ink:#333;
  --heading:#1254a5;
  --form-bg:#eeeeee;
  --white:#fff;
}
*{margin:0;padding:0;box-sizing:border-box}
html,body{width:691px;height:1200px;overflow:hidden;background:var(--white)}
body{position:relative;font-family:"Open Sans",Arial,sans-serif;color:var(--ink)}
.abs{position:absolute}

/* header */
.site-header{left:0;top:0;width:691px;height:44px;background:var(--blue)}
.brand{left:80px;top:0;height:44px;display:flex;align-items:center;gap:7px;font-family:"Montserrat",sans-serif;font-weight:600;font-size:14px;color:var(--white)}
.brand-dot{width:10px;height:10px;border-radius:50%;background:var(--white)}
.main-nav a{position:absolute;top:17px;font-family:"Montserrat",sans-serif;font-size:8px;font-weight:500;color:var(--white);text-decoration:none;white-space:nowrap}

/* hero */
.hero{left:0;top:44px;width:691px;height:272px;background:linear-gradient(180deg,#9dbf8a 0%,#c9d9b8 40%,#b8a89a 75%,#8d8a7a 100%)}
.hero-arrow{top:150px}
.hero-band{left:340px;top:186px;width:215px;height:92px;background:linear-gradient(90deg,rgba(255,255,255,.55),rgba(255,255,255,.15))}
.hero-title{left:347px;top:195px;font-family:"Oswald",sans-serif;font-weight:500;font-size:24px;line-height:30px;color:var(--heading)}
.hero-brand{left:398px;top:238px;font-family:"Kaushan Script",cursive;font-size:31px;line-height:34px;color:var(--script-green);transform:rotate(-6deg);transform-origin:left bottom}
.hero-dot{left:229px;top:255px;width:18px;height:18px;border-radius:50%;background:rgba(255,255,255,.75)}

/* call band */
.call-band{left:0;top:316px;width:691px;height:62px;display:flex;align-items:center;justify-content:center;gap:16px}
.call-text{font-family:"Kaushan Script",cursive;font-size:25px;color:#222}
.call-phone{font-family:"Oswald",sans-serif;font-weight:500;font-size:27px;color:var(--green)}

/* features */
.features{left:0;top:378px;width:691px;height:198px;background:var(--blue)}
.feature{top:0;width:189px;height:198px;padding:12px 0 0 12px}
.feature+.feature{border-left:1px solid var(--blue-dark)}
.feature h2{font-family:"Montserrat",sans-serif;font-weight:600;font-size:13px;color:var(--white);padding-bottom:10px;border-bottom:2px solid var(--blue-line);width:163px;letter-spacing:.3px}
.feature ul{list-style:none;margin-top:15px}
.feature li{font-family:"Montserrat",sans-serif;font-size:7.6px;color:#d7e6f7;display:flex;gap:8px;line-height:10px;margin-bottom:9px}
.feature li svg{flex:none;margin-top:1px}

/* content */
.intro{left:75px;width:352px}
.intro .lead{font-family:"Playfair Display",serif;font-style:italic;font-size:13px;color:#555}
.intro h2{font-family:"Montserrat",sans-serif;font-weight:500;font-size:14px;color:var(--heading);margin-bottom:10px}
.intro p{font-size:7.9px;line-height:12.5px;color:#333;margin-bottom:11px;text-align:justify}
.rule{left:75px;top:756px;width:352px;height:1px;background:#e2e2e2}
.signature{left:308px;top:1050px;font-family:"Kaushan Script",cursive;font-size:16px;color:#222}

/* estimate form */
.estimate{left:454px;top:597px;width:162px;height:488px;background:var(--form-bg)}
.estimate h2{height:38px;background:var(--green);color:var(--white);font-family:"Montserrat",sans-serif;font-weight:500;font-size:16px;letter-spacing:.4px;display:flex;align-items:center;justify-content:center}
.field{position:absolute;left:11px;width:140px;height:24px;background:var(--white);font-size:7.5px;color:#555;padding:7px 6px}
.field.tall{height:62px}
.submit{position:absolute;left:11px;top:454px;width:70px;height:24px;background:var(--green-dark);color:var(--white);font-family:"Montserrat",sans-serif;font-weight:700;font-size:11px;display:flex;align-items:center;justify-content:center}

/* footer */
.site-footer{left:0;top:1108px;width:691px;height:53px;background:var(--blue);color:var(--white);font-size:7.6px}
.foot-item{top:14px;display:flex;gap:10px;align-items:center;line-height:11px}
.follow{left:523px;top:18px;display:flex;align-items:center;gap:4px}
.follow span{margin-right:2px}
.social{width:17px;height:17px;border-radius:50%;background:var(--white)}
.foot-nav{left:0;top:1166px;width:691px;text-align:center;font-size:7.2px;color:#333}
.foot-nav a{color:#333;text-decoration:none;margin:0 3px}
.copyright{left:0;top:1182px;width:691px;text-align:center;font-size:6.8px;color:#444}
</style>
</head>
<body>

<header class="site-header abs">
  <div class="brand abs"><span class="brand-dot"></span>Tidy Nest</div>
  <nav class="main-nav">
    <a href="#" style="left:218px">HOME</a>
    <a href="#" style="left:266px">ABOUT US</a>
    <a href="#" style="left:329px">SERVICES</a>
    <a href="#" style="left:388px">TIPS</a>
    <a href="#" style="left:428px">REVIEWS</a>
    <a href="#" style="left:484px">PHOTOS</a>
    <a href="#" style="left:540px">FAQ</a>
    <a href="#" style="left:579px">CONTACT</a>
  </nav>
</header>

<section class="hero abs" role="img" aria-label="Photo of four smiling senior golfers carrying golf bags on a sunny course"></section>
<svg class="hero-arrow abs" style="left:75px" width="14" height="40" viewBox="0 0 14 40"><path d="M12 2 L2 20 L12 38" fill="none" stroke="#fff" stroke-width="2"/></svg>
<svg class="hero-arrow abs" style="left:600px" width="14" height="40" viewBox="0 0 14 40"><path d="M2 2 L12 20 L2 38" fill="none" stroke="#fff" stroke-width="2"/></svg>
<div class="hero-band abs"></div>
<div class="hero-title abs">House Clening</div>
<div class="hero-brand abs">Tidy Nest</div>
<div class="hero-dot abs"></div>

<div class="call-band abs">
  <span class="call-text">It's Simple... Call Today</span>
  <span class="call-phone">289-555-0143</span>
</div>

<section class="features abs">
  <div class="feature abs" style="left:63px">
    <h2>WHAT WE DO ?</h2>
    <ul>
      <li><svg width="7" height="7" viewBox="0 0 7 7"><path d="M1 3.5 L3 5.5 L6 1" fill="none" stroke="#a9c9ec" stroke-width="1"/></svg>Thoroughly clean your bathrooms,<br>kitchen, bedrooms and living areas</li>
      <li><svg width="7" height="7" viewBox="0 0 7 7"><path d="M1 3.5 L3 5.5 L6 1" fill="none" stroke="#a9c9ec" stroke-width="1"/></svg>Mop or vacuum your floors</li>
      <li><svg width="7" height="7" viewBox="0 0 7 7"><path d="M1 3.5 L3 5.5 L6 1" fill="none" stroke="#a9c9ec" stroke-width="1"/></svg>Dust surfaces</li>
      <li><svg width="7" height="7" viewBox="0 0 7 7"><path d="M1 3.5 L3 5.5 L6 1" fill="none" stroke="#a9c9ec" stroke-width="1"/></svg>Collect garbage</li>
      <li><svg width="7" height="7" viewBox="0 0 7 7"><path d="M1 3.5 L3 5.5 L6 1" fill="none" stroke="#a9c9ec" stroke-width="1"/></svg>Make beds</li>
    </ul>
  </div>
  <div class="feature abs" style="left:252px">
    <h2>WHY CHOOSE US?</h2>
    <ul>
      <li><svg width="7" height="7" viewBox="0 0 7 7"><path d="M1 3.5 L3 5.5 L6 1" fill="none" stroke="#a9c9ec" stroke-width="1"/></svg>Owners Present at Every Cleaning</li>
      <li><svg width="7" height="7" viewBox="0 0 7 7"><path d="M1 3.5 L3 5.5 L6 1" fill="none" stroke="#a9c9ec" stroke-width="1"/></svg>Locally Owned &amp; Operated</li>
      <li><svg width="7" height="7" viewBox="0 0 7 7"><path d="M1 3.5 L3 5.5 L6 1" fill="none" stroke="#a9c9ec" stroke-width="1"/></svg>Reliable &amp; Affordable</li>
      <li><svg width="7" height="7" viewBox="0 0 7 7"><path d="M1 3.5 L3 5.5 L6 1" fill="none" stroke="#a9c9ec" stroke-width="1"/></svg>All Supplies Provided</li>
      <li><svg width="7" height="7" viewBox="0 0 7 7"><path d="M1 3.5 L3 5.5 L6 1" fill="none" stroke="#a9c9ec" stroke-width="1"/></svg>Green Cleaning</li>
      <li><svg width="7" height="7" viewBox="0 0 7 7"><path d="M1 3.5 L3 5.5 L6 1" fill="none" stroke="#a9c9ec" stroke-width="1"/></svg>Pet Friendly</li>
      <li><svg width="7" height="7" viewBox="0 0 7 7"><path d="M1 3.5 L3 5.5 L6 1" fill="none" stroke="#a9c9ec" stroke-width="1"/></svg>No Contracts</li>
    </ul>
  </div>
  <div class="feature abs" style="left:441px">
    <h2>HOW MUCH ?</h2>
    <ul>
      <li><svg width="7" height="7" viewBox="0 0 7 7"><path d="M1 3.5 L3 5.5 L6 1" fill="none" stroke="#a9c9ec" stroke-width="1"/></svg>Locally Owned &amp; Operated</li>
      <li><svg width="7" height="7" viewBox="0 0 7 7"><path d="M1 3.5 L3 5.5 L6 1" fill="none" stroke="#a9c9ec" stroke-width="1"/></svg>Reliable &amp; Affordable</li>
      <li><svg width="7" height="7" viewBox="0 0 7 7"><path d="M1 3.5 L3 5.5 L6 1" fill="none" stroke="#a9c9ec" stroke-width="1"/></svg>All Supplies Provided</li>
      <li><svg width="7" height="7" viewBox="0 0 7 7"><path d="M1 3.5 L3 5.5 L6 1" fill="none" stroke="#a9c9ec" stroke-width="1"/></svg>Green Cleaning</li>
      <li><svg width="7" height="7" viewBox="0 0 7 7"><path d="M1 3.5 L3 5.5 L6 1" fill="none" stroke="#a9c9ec" stroke-width="1"/></svg>Pet Friendly</li>
      <li><svg width="7" height="7" viewBox="0 0 7 7"><path d="M1 3.5 L3 5.5 L6 1" fill="none" stroke="#a9c9ec" stroke-width="1"/></svg>No Contracts</li>
    </ul>
  </div>
</section>

<article class="intro abs" style="top:592px">
  <div class="lead">Welcome to</div>
  <h2>TIDY NEST HOUSE CLEANING</h2>
  <p>We are Daniel and Clara Westbrook and we have personally experienced the struggle of finding a reliable and affordable maid service. We understand how busy life can be and cleaning is one of the tasks that falls off the list when you're stretched too thin. We are here to help! Let Tidy Nest take care of the house cleaning so you can focus on the more important things in life.</p>
  <p>Halton, Burlington, Oakville and Milton residents can count on us to make your home sparkle from top to bottom!</p>
</article>
<div class="rule abs"></div>
<article class="intro abs" style="top:780px">
  <div class="lead">Meet</div>
  <h2>CLARA AND DANIEL WESTBROOK</h2>
  <p>It's about caring, not just cleaning.</p>
  <p>Having personally experienced the struggles of Finding quality maid service for our home, we wantto make it simpler for families in the Halton area. Our goal is to provide caring, consistent and reliable house cleaning to every customer we serve.</p>
  <p>We pride ourselves on delivering the best possible customer experience in the region and providing outstanding healthy home cleaning to this important and rapidly growing community.</p>
  <p>We are passionate about making a difference in the community and having Tidy Nest become synonymous with reliable and dependable housekeeping services. With local focus and attention to quality and service we believe the families in the Halton region including Oakville, Burlington and Milton can be confident they are receiving the best and most reliable services in the region.</p>
  <p>We are proud to serve the communities of Oakville, Burlington and Milton.</p>
</article>
<div class="signature abs">– Clara &amp; Daniel</div>

<aside class="estimate abs">
  <h2>FREE ESTIMATE</h2>
  <div class="field" style="top:51px">First Name &amp; Last Name:</div>
  <div class="field" style="top:84px">Address line1:</div>
  <div class="field" style="top:116px">Address line2:</div>
  <div class="field" style="top:149px">City:</div>
  <div class="field" style="top:181px">State/Province:</div>
  <div class="field" style="top:214px">Zip/Postal Code:</div>
  <div class="field" style="top:246px">Phone:</div>
  <div class="field" style="top:279px">Email:</div>
  <div class="field tall" style="top:311px">How did you hear about us?</div>
  <div class="field tall" style="top:381px">Comments:</div>
  <div class="submit">SUBMIT</div>
</aside>

<footer class="site-footer abs">
  <div class="foot-item abs" style="left:76px">
    <svg width="13" height="17" viewBox="0 0 13 17"><path d="M6.5 1 C3.2 1 1 3.4 1 6.3 C1 10 6.5 16 6.5 16 C6.5 16 12 10 12 6.3 C12 3.4 9.8 1 6.5 1Z" fill="none" stroke="#fff" stroke-width="1.5"/><circle cx="6.5" cy="6.3" r="2" fill="#fff"/></svg>
    <span>Tidy Nest House<br>Lorem Ipsum amet...</span>
  </div>
  <div class="foot-item abs" style="left:230px">
    <svg width="12" height="18" viewBox="0 0 12 18"><rect x="1" y="1" width="10" height="16" rx="2" fill="none" stroke="#fff" stroke-width="1.5"/><circle cx="6" cy="14" r="1" fill="#fff"/></svg>
    <span>Phone:<br>289-555-0143</span>
  </div>
  <div class="foot-item abs" style="left:355px">
    <svg width="18" height="13" viewBox="0 0 18 13"><rect x="1" y="1" width="16" height="11" fill="none" stroke="#fff" stroke-width="1.5"/><path d="M1 1 L9 7 L17 1" fill="none" stroke="#fff" stroke-width="1.5"/></svg>
    <span>Email:<br>info@tidynest.com</span>
  </div>
  <div class="follow abs"><span>Follow :</span><div class="social"></div><div class="social"></div><div class="social"></div></div>
</footer>

<nav class="foot-nav abs">
  <a href="#">Home</a>|<a href="#">About Us</a>|<a href="#">Services</a>|<a href="#">Tips</a>|<a href="#">Reviews</a>|<a href="#">Photos</a>|<a href="#">FAQ</a>|<a href="#">Contact</a>
</nav>
<div class="copyright abs">© 2013Tidy Nest House Cleaning. All Rights Reserved.</div>

</body>
</html>
```